We need letterhead, Business Cards, and envelops designed. We have attached a design of our logo and a sample of letterhead idea that was started but never perfected, it is only an idea for the letterhead if you can design something better we may love that also we are open to change.
We want a design that looks professional in style. we are a non profit trade association in the construction industry. the green color in the attached design represent green building, and we like that. also if you just want to enhance the letterhead sample that we attached that would be fine also.
Thanks and good luck
also the name that should show on the first business cards should be Morgan Feltwick, Director are web address is www.pvtrn.org

```html
<!DOCTYPE html>
<html lang="en">
<head>
<meta charset="utf-8">
<title>PVTRN Stationery</title>
<link href="https://fonts.googleapis.com/css2?family=Open+Sans:ital,wght@0,400;0,600;0,700;1,700&display=swap" rel="stylesheet">
<style>
  :root {
    --backdrop: #b3b3b3;
    --paper: #ffffff;
    --paper-shade: #e4e4e4;
    --ink: #1c1c1c;
    --body-ink: #333333;
    --leaf: #8cc63f;
    --forest: #1f6b30;
    --web-green: #2d6b3a;
  }
  * { margin: 0; padding: 0; box-sizing: border-box; }
  html, body { width: 1200px; height: 1018px; overflow: hidden; }
  body {
    background: var(--backdrop);
    font-family: "Open Sans", Arial, sans-serif;
    color: var(--body-ink);
    position: relative;
  }
  .sheet, .card, .envelope { position: absolute; background: var(--paper); overflow: hidden; }

  .logo { position: absolute; display: flex; align-items: center; gap: 0.18em; line-height: 1; }
  .logo-name { font-weight: 600; color: var(--ink); letter-spacing: 0.02em; }
  .logo-square { width: 0.55em; height: 0.55em; background: var(--leaf); }

  .rule { position: absolute; right: 0; background: var(--leaf); }

  /* bottom decoration area: plain soft gradient band */
  .green-band {
    position: absolute; left: 0; bottom: 0; width: 100%;
    background: linear-gradient(90deg, rgba(140,198,63,0) 0%, var(--leaf) 35%, var(--forest) 100%);
  }

  /* letterhead */
  .letterhead { left: 168px; top: 120px; width: 378px; height: 538px; }
  .letterhead .logo { left: 30px; top: 36px; font-size: 34px; }
  .letterhead .rule { left: 154px; top: 66px; height: 5px; }
  .letter { position: absolute; left: 30px; width: 330px; font-size: 7.4px; line-height: 9.6px; }
  .letter-nowrap { white-space: nowrap; }
  .letterhead .green-band { height: 22px; }
  .site { position: absolute; right: 62px; bottom: 30px; font-size: 7px; color: var(--web-green); font-weight: 600; }

  /* second sheet */
  .second-sheet { left: 598px; top: 106px; width: 440px; height: 558px; }
  .second-sheet .logo { left: 18px; top: 476px; font-size: 50px; }
  .second-sheet .rule { left: 198px; top: 517px; height: 9px; }

  /* cards */
  .card-front { left: 66px; top: 706px; width: 148px; height: 89px; }
  .card-front .logo { left: 24px; top: 31px; font-size: 26px; }
  .card-back { left: 64px; top: 818px; width: 145px; height: 88px; }
  .card-back .logo { left: 10px; top: 8px; font-size: 15px; }
  .holder { position: absolute; left: 11px; top: 37px; font-size: 8px; color: var(--ink); line-height: 9px; }
  .holder-role { font-size: 6px; font-weight: 700; font-style: italic; }
  .contacts { position: absolute; left: 11px; top: 61px; width: 128px; display: grid; grid-template-columns: 1fr 1fr; column-gap: 6px; font-size: 3.8px; line-height: 8px; color: var(--body-ink); white-space: nowrap; }

  /* envelopes */
  .envelope { background: linear-gradient(180deg, var(--paper) 0%, var(--paper-shade) 100%); }
  .envelope-front { left: 252px; top: 702px; width: 422px; height: 206px; }
  .envelope-front .logo { left: 16px; top: 16px; font-size: 27px; }
  .envelope-back { left: 715px; top: 701px; width: 421px; height: 208px; }
  .envelope-back .logo { left: 177px; top: 19px; font-size: 27px; }
  .flap { position: absolute; left: 0; top: 0; width: 100%; height: 66px; }
  .envelope .green-band { height: 24px; }
</style>
</head>
<body>

<section class="sheet letterhead">
  <div class="logo"><span class="logo-name">PVTRN</span><span class="logo-square"></span></div>
  <div class="rule"></div>

  <p class="letter" style="top:108px">2250 Cedar Hollow Road<br>Fresno, CA 93701.</p>
  <p class="letter" style="top:136px">January 29th, 2011</p>
  <p class="letter" style="top:164px">Mr. Halloway<br>President, Halloway Youth Center<br>518 Orchard Lane<br>Portland, OR 97205</p>
  <p class="letter" style="top:215px">Dear Mr. Halloway:</p>
  <p class="letter" style="top:235px">In the first paragraph, one needs to give a brief introduction of oneself. One should also give reference to the purpose of the letter in brief.<br>The second paragraph needs to give the details of the letter and its need. This paragraph is mostly longer than the others and plays the main role in the letter. Keep the sentences short and to the point. Avoid using complex words and sentences.</p>
  <p class="letter" style="top:292px">The third and last paragraph is the conclusion of the letter and can be kept short.</p>
  <p class="letter" style="top:311px">Sincerely,</p>
  <p class="letter" style="top:329px">(this is where the signature of the writer will be placed)</p>
  <p class="letter letter-nowrap" style="top:348px">Lena Ashcombe<br>Read more at Lettercraft: http://www.lettercraft.net/articles/letter-format-example.html</p>

  <div class="green-band" role="img" aria-label="Green decorative wave band"></div>
  <span class="site">www.pvtrn.org</span>
</section>

<section class="sheet second-sheet">
  <div class="logo"><span class="logo-name">PVTRN</span><span class="logo-square"></span></div>
  <div class="rule"></div>
</section>

<section class="card card-front">
  <div class="logo"><span class="logo-name">PVTRN</span><span class="logo-square"></span></div>
</section>

<section class="card card-back">
  <div class="logo"><span class="logo-name">PVTRN</span><span class="logo-square"></span></div>
  <div class="holder">Your Name<br><span class="holder-role">Position</span></div>
  <div class="contacts">
    <span>Address: 2250 Cedar Hollow</span><span>Fax: 559 555 0143</span>
    <span>Phone: 559 555 0142</span><span>Email: info@pvtrn.org</span>
    <span></span><span>Web: www.pvtrn.org</span>
  </div>
</section>

<section class="envelope envelope-front">
  <div class="logo"><span class="logo-name">PVTRN</span><span class="logo-square"></span></div>
  <div class="green-band" role="img" aria-label="Green decorative wave band"></div>
</section>

<section class="envelope envelope-back">
  <svg class="flap" viewBox="0 0 421 66" preserveAspectRatio="none" aria-hidden="true">
    <polygon points="0,0 421,0 404,62 17,62" fill="#fbfbfb"/>
    <polyline points="0,0 17,62 404,62 421,0" fill="none" stroke="#cfcfcf" stroke-width="1.5"/>
  </svg>
  <div class="logo"><span class="logo-name">PVTRN</span><span class="logo-square"></span></div>
  <div class="green-band" role="img" aria-label="Green decorative wave band"></div>
</section>

</body>
</html>
```